Ward Compass Business Card Design*

We need a business card design for our company Ward Compass. Our company is specialized in providing online consulting services regarding medical institutions, hospitals and doctors. We work with patients worldwide looking to choose between healthcare providers. We have a website you may use as a reference, where we list doctors and clinics worldwide. So we target Medical providers as well as patients worldwide.
Target Market(s)
Medical Providers and patients around the world
Industry/Entity Type
Medical
Contact Information for Business Card
Salwa Kettani
CEO
+90 612 348 2175
info@wardcompass.example
www.wardcompass.example
14 Annakhil 7 H.R.B. Rabat, Morocco
Requirements
Must have
- Company logo/name on one full side, personal info and smaller logo and company name on the other side.
Nice to have
- Smart and elegant design

```html
<!DOCTYPE html>
<html lang="en">
<head>
<meta charset="utf-8">
<title>Ward Compass — Business Card</title>
<link rel="stylesheet" href="https://fonts.googleapis.com/css2?family=Montserrat:wght@400;600;700&display=swap">
<style>
  :root {
    --navy: #1c3767;
    --paper: #f7f7f8;
    --paper-shade: #e4e5e8;
    --backdrop: #3a3b3e;
    --ink-light: #ffffff;
    --ink-soft: #dfe5ef;
  }
  * { box-sizing: border-box; margin: 0; padding: 0; }
  html, body {
    width: 1200px; height: 997px; overflow: hidden;
    background: var(--backdrop);
    font-family: "Montserrat", Arial, sans-serif;
  }
  .sheet {
    width: 1200px; height: 997px;
    display: flex; flex-direction: column; align-items: center; justify-content: center;
    gap: 64px;
  }
  .card {
    position: relative;
    width: 620px; height: 354px;
    border-radius: 20px;
    overflow: hidden;
    background: linear-gradient(135deg, var(--paper) 55%, var(--paper-shade));
    box-shadow: 0 18px 40px rgba(0,0,0,.45);
    display: flex;
  }
  .panel {
    position: relative;
    background: var(--navy);
    color: var(--ink-light);
  }
  .panel .notch {
    position: absolute; width: 0; height: 0;
    border-top: 9px solid transparent; border-bottom: 9px solid transparent;
  }
  .field {
    flex: 1;
    display: flex; align-items: center; justify-content: center;
  }
  .wordmark {
    display: flex; align-items: center; gap: 14px;
    color: var(--navy);
    font-weight: 700; font-size: 30px; letter-spacing: 1px;
    text-transform: uppercase;
  }
  .wordmark .dot {
    width: 46px; height: 46px; border-radius: 50%;
    background: var(--navy);
  }

  /* front */
  .card--front .panel { width: 31%; }
  .card--front .panel .notch {
    right: -9px; top: 50%; margin-top: -9px;
    border-left: 9px solid var(--navy);
  }
  .tagline {
    position: absolute; right: 22px; top: 50%; transform: translateY(-50%);
    text-align: right; text-transform: uppercase;
    font-size: 12.5px; line-height: 1.65; letter-spacing: .6px; color: var(--ink-soft);
  }

  /* back */
  .card--back .field { justify-content: flex-start; padding-left: 44px; }
  .card--back .wordmark { font-size: 26px; gap: 12px; }
  .card--back .wordmark .dot { width: 40px; height: 40px; }
  .card--back .panel { width: 37%; padding: 96px 0 0 20px; }
  .card--back .panel .notch {
    left: -9px; top: 104px;
    border-right: 9px solid var(--navy);
  }
  .person-name { font-weight: 700; font-size: 15px; letter-spacing: .5px; text-transform: uppercase; }
  .person-role { font-weight: 600; font-size: 11px; margin-top: 2px; }
  .contacts { list-style: none; margin-top: 34px; font-size: 11.5px; color: var(--ink-soft); }
  .contacts li { display: flex; align-items: center; gap: 9px; margin-bottom: 6px; }
  .contacts svg { width: 15px; height: 15px; flex: none; }
</style>
</head>
<body>
<main class="sheet">

  <section class="card card--front" aria-label="Card front">
    <div class="panel">
      <span class="notch"></span>
      <p class="tagline">Find &amp; compare<br>top rated clinics<br>world wide</p>
    </div>
    <div class="field">
      <div class="wordmark"><span class="dot"></span>Ward Compass</div>
    </div>
  </section>

  <section class="card card--back" aria-label="Card back">
    <div class="field">
      <div class="wordmark"><span class="dot"></span>Ward Compass</div>
    </div>
    <div class="panel">
      <span class="notch"></span>
      <p class="person-name">Salwa Kettani</p>
      <p class="person-role">CEO</p>
      <ul class="contacts">
        <li>
          <svg viewBox="0 0 16 16"><circle cx="8" cy="8" r="8" fill="#fff"/><path d="M5 4.5h2l.6 2-1 .8a5 5 0 0 0 2.1 2.1l.8-1 2 .6v2c0 .4-.3.5-.6.5A6.5 6.5 0 0 1 4.5 5.1c0-.3.1-.6.5-.6z" fill="#1c3767"/></svg>
          +90 612 348 2175
        </li>
        <li>
          <svg viewBox="0 0 16 16"><circle cx="8" cy="8" r="8" fill="#fff"/><rect x="4" y="5.2" width="8" height="5.6" rx=".6" fill="none" stroke="#1c3767" stroke-width="1.1"/><path d="M4.3 5.6 8 8.4l3.7-2.8" fill="none" stroke="#1c3767" stroke-width="1.1"/></svg>
          info@wardcompass.example
        </li>
        <li>
          <svg viewBox="0 0 16 16"><circle cx="8" cy="8" r="8" fill="#fff"/><circle cx="8" cy="8" r="4" fill="none" stroke="#1c3767" stroke-width="1"/><ellipse cx="8" cy="8" rx="1.7" ry="4" fill="none" stroke="#1c3767" stroke-width="1"/><path d="M4 8h8" stroke="#1c3767" stroke-width="1"/></svg>
          www.wardcompass.example
        </li>
      </ul>
    </div>
  </section>

</main>
</body>
</html>
```